Business Card Design Project

I need a business card designed from scratch. I have an existing logo that I can upload in Illustrator for modification or redesign.

The Company is called Query Lanterns http://querylanterns.com.au and we provide Search Engine Optimization services to Australian businesses. The current logo signifies an increase in visitors, profits etc...

There are no restrictions as to the redesign - colours, style etc are all open to change.

Cards will be full colour and one sided printed at http://www.cardmoxel.com.au so check their requirements for file format and sizes etc.

I will expect all original files upon completion of project.

Target Market(s)

Any business with a web site looking to improve their search engine rankings

Industry/Entity Type

Business

Requirements
Must have
• I like modern, sleek designs. Clean, not fussy, uncluttered.

```html
<!DOCTYPE html>
<html lang="en">
<head>
<meta charset="utf-8">
<title>Query Lanterns – Business Card</title>
<link rel="stylesheet" href="https://fonts.googleapis.com/css2?family=Source+Sans+3:wght@400;600;700&display=swap">
<style>
  :root {
    --backdrop: #b1892c;
    --card: #ffffff;
    --ink: #222222;
    --brand-blue: #1c6fb6;
    --brand-yellow: #f6c21c;
    --brand-yellow-light: #f2da4a;
    --divider: #8a8a8a;
    --card-shadow: rgba(0, 0, 0, 0.55);
  }
  * { box-sizing: border-box; margin: 0; padding: 0; }
  html, body { width: 1200px; height: 686px; overflow: hidden; }
  body {
    background: var(--backdrop);
    font-family: "Source Sans 3", "Myriad Pro", Arial, sans-serif;
    color: var(--ink);
    position: relative;
  }
  .card {
    position: absolute;
    width: 494px;
    height: 281px;
    background: var(--card);
    border-radius: 18px;
    box-shadow: 2px 3px 2px var(--card-shadow);
    overflow: hidden;
  }
  .card--front { left: 81px; top: 139px; }
  .card--back { left: 617px; top: 267px; }

  .name-tab {
    position: absolute;
    left: 245px;
    top: 49px;
    width: 249px;
    height: 75px;
  }
  .name-tab svg { position: absolute; inset: 0; }
  .name-tab__label {
    position: absolute;
    left: 72px;
    top: 24px;
    display: flex;
    align-items: center;
    color: #ffffff;
    white-space: nowrap;
  }
  .name-tab__name { font-size: 17px; font-weight: 700; }
  .name-tab__sep {
    width: 1px; height: 16px; background: #ffffff;
    margin: 0 9px 0 10px;
  }
  .name-tab__title { font-size: 12px; font-weight: 700; }

  .wordmark {
    position: absolute;
    display: flex;
    align-items: center;
    gap: 8px;
    color: var(--brand-blue);
    font-weight: 700;
    white-space: nowrap;
  }
  .wordmark__dot {
    border-radius: 50%;
    background: var(--brand-yellow);
    flex: none;
  }
  .card--front .wordmark { left: 16px; top: 184px; font-size: 23px; }
  .card--front .wordmark__dot { width: 14px; height: 14px; }

  .divider {
    position: absolute;
    left: 237px; top: 162px;
    width: 1px; height: 74px;
    background: var(--divider);
  }

  .contact {
    position: absolute;
    left: 249px;
    top: 146px;
    font-size: 12.5px;
    line-height: 18px;
    list-style: none;
  }
  .contact li { display: flex; align-items: center; gap: 4px; }
  .contact svg { width: 10px; height: 10px; flex: none; }
  .address {
    position: absolute;
    left: 250px;
    top: 209px;
    font-size: 12.5px;
    line-height: 17px;
    font-style: normal;
  }

  .card--back .wordmark {
    left: 0; right: 0; top: 122px;
    justify-content: center;
    font-size: 34px;
    gap: 12px;
  }
  .card--back .wordmark__dot { width: 22px; height: 22px; }
</style>
</head>
<body>

<section class="card card--front" aria-label="Business card front">
  <div class="name-tab">
    <svg viewBox="0 0 249 75" width="249" height="75" aria-hidden="true">
      <path d="M36 19 H240 Q249 19 249 8 V61 Q249 56 240 56 H36 Z" fill="var(--brand-yellow)"/>
      <circle cx="37" cy="37.5" r="36" fill="var(--brand-yellow-light)" stroke="#d8b21a" stroke-width="1"/>
      <circle cx="37" cy="37.5" r="15" fill="#ffffff" stroke="#c9a318" stroke-width="1"/>
    </svg>
    <div class="name-tab__label">
      <span class="name-tab__name">Your Name</span>
      <span class="name-tab__sep"></span>
      <span class="name-tab__title">Title</span>
    </div>
  </div>

  <div class="wordmark">
    <span class="wordmark__dot"></span>
    <span class="wordmark__text">Query Lanterns</span>
  </div>

  <div class="divider"></div>

  <ul class="contact">
    <li>
      <svg viewBox="0 0 10 10" aria-hidden="true"><path d="M2 0.5 L4 2.5 L3 4 Q4 6 6 7 L7.5 6 L9.5 8 L8 9.5 Q3 9 0.5 2 Z" fill="var(--brand-blue)"/></svg>
      <span>123-456-7890</span>
    </li>
    <li>
      <svg viewBox="0 0 10 10" aria-hidden="true"><rect x="0" y="2" width="10" height="6.5" fill="var(--brand-blue)"/><path d="M0.5 2.5 L5 6 L9.5 2.5" stroke="#fff" stroke-width="0.9" fill="none"/></svg>
      <span>inquiry@querylanterns.com.au.com</span>
    </li>
    <li>
      <svg viewBox="0 0 10 10" aria-hidden="true"><circle cx="5" cy="5" r="4.6" fill="var(--brand-blue)"/><path d="M0.6 5 H9.4 M5 0.4 V9.6 M5 0.4 Q2 5 5 9.6 M5 0.4 Q8 5 5 9.6" stroke="#fff" stroke-width="0.7" fill="none"/></svg>
      <span>www.querylanterns.com.au</span>
    </li>
  </ul>

  <address class="address">
    Street name City<br>
    State, zip code
  </address>
</section>

<section class="card card--back" aria-label="Business card back">
  <div class="wordmark">
    <span class="wordmark__dot"></span>
    <span class="wordmark__text">Query Lanterns</span>
  </div>
</section>

</body>
</html>
```